Brightmoor Hall Lead Generator + Checklist

I have typed up a 9 page word doc to be a lead generator for my website called "7 Quiet Slip-Ups Party Hosts Overlook" and I am looking for someone to clean it up, and make it professional and inline with our brand.

Logo Hex: #971F20

Industry/Entity Type

Event Planning

Font styles to use
Other font styles liked:
• Helvetica Neue is our brands font, but it doesn't have to be that. Something similar that is rounded would be good like Arial I think.

Requirements
Must have
• Clean, but elegant design.
• Because it is very text heavy, have the topics easily broken out and maybe staggered so that it is easy to identify main topics and sub topics.
Should not have
• Not just looking for basic formating around the edges of the document, but to also have the text displayed in an easily readable way with clear sections.

```html
<!DOCTYPE html>
<html lang="en">
<head>
<meta charset="utf-8">
<title>Brightmoor Hall – Guide Spread</title>
<link rel="stylesheet" href="https://fonts.googleapis.com/css2?family=Arimo:ital,wght@0,400;0,700;1,400&family=Roboto:wght@300&display=swap">
<style>
  :root {
    --brand-red: #971f20;
    --bar-red: #9b2223;
    --ink: #231f20;
    --numeral-grey: #e4e4e6;
    --paper: #ffffff;
  }
  * { box-sizing: border-box; margin: 0; padding: 0; }
  html, body { width: 1200px; height: 777px; overflow: hidden; background: var(--paper); }
  body { font-family: "Arimo", Arial, sans-serif; color: var(--ink); }
  .spread { position: relative; width: 1200px; height: 777px; overflow: hidden; }
  .page { position: absolute; top: 0; width: 600px; height: 777px; }
  .page--left { left: 0; }
  .page--right { left: 600px; }

  /* Left page */
  .intro { position: absolute; left: 34px; top: 177px; width: 530px; font-size: 11.2px; line-height: 13.8px; }
  .intro h2 { font-size: 17.6px; font-weight: 700; line-height: 20px; margin-bottom: 11px; }
  .intro p { margin-bottom: 13.5px; }
  .intro .lead { font-weight: 700; margin-bottom: 12px; }
  .mistakes { list-style: none; margin-left: 17px; }
  .mistakes li { position: relative; padding-left: 18px; margin-bottom: 5.5px; }
  .mistakes li span.num { position: absolute; left: 0; color: var(--brand-red); font-weight: 700; }

  /* Right page */
  .tips-title { position: absolute; left: 42px; top: 58px; font-family: "Roboto", "Arimo", sans-serif; font-weight: 300; font-size: 32.5px; line-height: 35px; color: var(--brand-red); letter-spacing: -0.6px; text-transform: uppercase; }
  .tips-title strong { font-family: "Arimo", Arial, sans-serif; font-weight: 700; }
  .tip-bar { position: absolute; left: 42px; top: 139px; width: 525px; height: 17.5px; background: var(--bar-red); color: #fff; font-weight: 700; font-size: 12.4px; line-height: 17.5px; padding-left: 6px; }
  .tip-bar .num { display: inline-block; width: 28px; }
  .tip-body { position: absolute; left: 80px; top: 169px; width: 490px; font-size: 11.2px; line-height: 13.6px; }
  .point { position: relative; padding-left: 17px; margin-bottom: 8px; }
  .point > .mark { position: absolute; left: 0; font-weight: 700; }
  .subpoints { list-style: none; margin: 8px 0 0 50px; }
  .subpoints li { position: relative; padding-left: 0; margin-bottom: 6.5px; }
  .subpoints li .mark { position: absolute; left: -30px; width: 20px; text-align: right; }
  .numeral { position: absolute; left: 628px; top: 545px; font-family: "Roboto", "Arimo", sans-serif; font-weight: 300; font-size: 300px; line-height: 300px; color: var(--numeral-grey); }

  /* Footers */
  .folio { position: absolute; top: 742px; font-size: 7.6px; line-height: 9px; }
  .folio strong { color: var(--brand-red); }
  .folio--left { left: 34px; }
  .folio--right { right: 38px; }
  .corner { position: absolute; bottom: 0; }
  .corner--left { left: 0; }
  .corner--right { right: 0; }
</style>
</head>
<body>
<div class="spread">
  <section class="page page--left">
    <div class="intro">
      <h2>You have enough on your plate already.</h2>
      <p>The last thing you need is to waste time chasing down basic information from venues to try and present options to your boss, planning team or board. You could just go to the same place you always go to, but that gets old and you’d like to try something new.</p>
      <p>It seemed so easy, but a week goes by and you still don’t have good options because some venues still haven’t returned your calls and many of the venues website’s lack basic information about their private event space such as capacity, pricing and other important policies.</p>
      <p>You consider just driving to the venues to get the information, but who has five extra hours to do that? You definitely don’t.</p>
      <p>Don’t worry, <strong>you’re not alone.</strong> After planning many local events and experiencing that same back and forth with venues, I thought there had to be a better way. That’s why I created Brightmoor Hall and put together this guide with the help of other local leaders who have planned events in Aldenport.</p>
      <p class="lead">Here are the common mistakes we’ll go over, and how to avoid them so you’ll throw an event people will talk about for years.</p>
      <ol class="mistakes">
        <li><span class="num">1.</span>As simple as it sounds - many planners don’t start by first thinking about the type of event they are planning, especially if is their first time planning an event.</li>
        <li><span class="num">2.</span>Often they don’t fully consider the expectations of their audience.</li>
        <li><span class="num">3.</span>Planners assume the policies from one venue to the next are similar, when in reality they can be very different - and they forget to ask the <em>right</em> questions.</li>
        <li><span class="num">4.</span>They forget that just like your car runs on gas, your event runs on great food and drinks.</li>
        <li><span class="num">5.</span>Lastly, they don’t track and ensure the details are completed.</li>
      </ol>
    </div>
    <p class="folio folio--left"><strong>2</strong> | Brightmoor Hall</p>
    <svg class="corner corner--left" width="32" height="56" viewBox="0 0 32 56" aria-hidden="true">
      <path d="M0 0 C14 2 26 14 30 30 L22 56 L0 56 Z" fill="var(--brand-red)"/>
    </svg>
  </section>

  <section class="page page--right">
    <h1 class="tips-title">Here are the <strong>5</strong> simple tips to<br>avoid these common mistakes</h1>
    <div class="tip-bar"><span class="num">1.</span>Know the type of event you’re planning</div>
    <div class="numeral" aria-hidden="true">1</div>
    <div class="tip-body">
      <div class="point">
        <span class="mark">a.</span>People who start planning an event without taking the time to think about the <em>type</em> of event they’re planning often run into problems.
        <ol class="subpoints">
          <li><span class="mark">i.</span>For example, if you are planning a one time event and you aren’t regularly reaching out to your attendees and actively get the word out about the event, attendance will be low. If it is a recurring weekly event on the other hand, that level of communication probably isn’t needed as people will already be used to coming.</li>
          <li><span class="mark">ii.</span>I recently went to a one-time event and after registering didn’t hear anything from the event organizer, even on the day of the event! As an attendee I start to wonder if the event is even happening or not, I didn’t have a good feel for what to wear and I didn’t know which room to go to once I get to the venue. These are not the kind of thoughts you want running through your attendees heads just before the event, you want them excited and looking forward to your event - not uncertain about basic details.</li>
          <li><span class="mark">iii.</span>This might seem obvious, but it’s amazing how often this simple step of knowing the type of event you’re planning can get overlooked. It matters because the priorities and necessary steps for a recurring weekly networking event will be much different than a big end of year event.</li>
        </ol>
      </div>
      <div class="point">
        <span class="mark">b.</span>By knowing up front the type of event you’re planning - you’ll start looking at venues that are a great fit for that type of event and make sure you take the necessary steps to throw a great event!
      </div>
    </div>
    <p class="folio folio--right">7 Quiet Slip-Ups Party Hosts Overlook &nbsp;| <strong>3</strong></p>
    <svg class="corner corner--right" width="32" height="56" viewBox="0 0 32 56" aria-hidden="true">
      <path d="M32 0 C18 2 6 14 2 30 L10 56 L32 56 Z" fill="var(--brand-red)"/>
    </svg>
  </section>
</div>
</body>
</html>
```